Re-style home page - eye-catching and unique design for social commerce website

We need a new concept design for BrinoKet's home page.
We don't want to make huge changes but creating a more professional and eye-catching style.

We need to look very serious like a professional services company and in the same time to look like a social network for e-commerce.

Our logo is very captive and you can use to creating something of harmonious.

This is a re-style and I'm excepted to see unique and fresh design like Glimmora.

Target Market(s)

e-commerce and social

Industry/Entity Type

Social

Number of Pages Required

1 page

Font styles to use
Serif
Sans Serif

Requirements
Must have
• An eye-catching result.
• Search bar with logo and Login How it works and business
• The slogan with login and signup.
• Footer links.
Nice to have
• I would like to open the home page and see only two clear ways:
• -Consumer
• --Search
• --The slogan
• --Login and Signup
• --How it works
• -Business
• --Go to Business area
• Background: City, Shopping.
Should not have
• Scrollbar style!

```html
<!DOCTYPE html>
<html lang="en">
<head>
<meta charset="utf-8">
<title>BrinoKet – Home</title>
<link rel="stylesheet" href="https://fonts.googleapis.com/css2?family=Montserrat:wght@400;500;600;700&display=swap">
<style>
  :root {
    --nav-bg: #0d0f2e;
    --dropdown-bg: #1c1f40;
    --text-white: #ffffff;
    --text-muted: #b9b8cc;
    --green: #7cb733;
    --social-blue: #4a5f9c;
    --input-bg: #ffffff;
    --placeholder: #9a9a9a;
    --scene-dark: #231f45;
    --scene-mid: #4b3c5e;
    --scene-warm: #7a5a5c;
  }
  * { box-sizing: border-box; margin: 0; padding: 0; }
  html, body { width: 1200px; height: 675px; overflow: hidden; }
  body {
    position: relative;
    font-family: "Montserrat", Arial, sans-serif;
    color: var(--text-white);
    background: var(--scene-dark);
  }
  .city-backdrop {
    position: absolute; inset: 0;
    background:
      radial-gradient(ellipse at 20% 35%, rgba(160,120,90,0.45), transparent 45%),
      radial-gradient(ellipse at 85% 30%, rgba(170,150,170,0.35), transparent 40%),
      linear-gradient(180deg, var(--scene-mid) 0%, var(--scene-dark) 55%, #3a2f4c 80%, var(--scene-warm) 100%);
  }
  .top-nav {
    position: absolute; left: 0; top: 0; width: 1200px; height: 59px;
    background: var(--nav-bg);
  }
  .feed-label { position: absolute; left: 33px; top: 20px; font-size: 13px; font-weight: 600; }
  .feed-select {
    position: absolute; left: 148px; top: 15px; width: 145px; height: 26px;
    background: var(--dropdown-bg); border-radius: 4px;
    font-size: 11px; color: var(--text-muted); padding: 6px 14px;
  }
  .feed-select svg { position: absolute; right: 12px; top: 10px; }
  .nav-links a {
    position: absolute; top: 21px; font-size: 13px; font-weight: 600;
    color: var(--text-white); text-decoration: none;
  }
  .hero-card {
    position: absolute; left: 350px; top: 112px; width: 500px; height: 387px;
    border-radius: 14px; overflow: hidden;
  }
  .hero-photo {
    position: absolute; inset: 0;
    background:
      radial-gradient(circle at 82% 82%, rgba(140,80,60,0.85), transparent 28%),
      radial-gradient(circle at 70% 15%, rgba(230,70,70,0.8), transparent 35%),
      linear-gradient(135deg, #c9917a 0%, #e58a6e 40%, #e0625e 70%, #c85a55 100%);
  }
  .hero-content { position: absolute; inset: 0; text-align: center; }
  .brand-name {
    position: absolute; top: 45px; left: 0; width: 100%;
    font-size: 32px; font-weight: 700; letter-spacing: -0.5px;
  }
  .hero-title { position: absolute; top: 108px; width: 100%; font-size: 24px; font-weight: 600; }
  .hero-tagline { position: absolute; top: 142px; width: 100%; font-size: 14px; font-weight: 500; }
  .search-bar { position: absolute; left: 72px; top: 197px; width: 354px; height: 34px; display: flex; }
  .search-input {
    flex: 1; background: var(--input-bg); border-radius: 2px 0 0 2px;
    font-size: 12px; color: var(--placeholder); padding: 10px 14px; text-align: left;
  }
  .search-button {
    width: 75px; background: var(--green); border-radius: 0 2px 2px 0;
    font-size: 13px; font-weight: 600; padding-top: 9px;
  }
  .social-button {
    position: absolute; left: 167px; top: 260px; width: 162px; height: 35px;
    background: var(--social-blue); border-radius: 2px;
    font-size: 10.5px; font-weight: 600; padding: 11px 0 0 34px; text-align: left;
  }
  .social-button .mark {
    position: absolute; left: 12px; top: 12px; width: 11px; height: 11px; background: var(--text-white);
  }
  .signup-button {
    position: absolute; left: 167px; top: 313px; width: 162px; height: 34px;
    border: 2px solid var(--text-white); border-radius: 3px;
    font-size: 10.5px; font-weight: 600; padding-top: 9px;
  }
  .business-button {
    position: absolute; left: 518px; top: 523px; width: 163px; height: 36px;
    background: var(--green); border-radius: 2px;
    font-size: 10.5px; font-weight: 600; padding: 12px 0 0 13px;
  }
  .business-button svg { position: absolute; right: 12px; top: 13px; }
  .footer-links a {
    position: absolute; top: 612px; font-size: 10px; color: var(--text-muted); text-decoration: none;
  }
  .footer-links a.current { color: var(--text-white); font-weight: 500; }
  .copyright { position: absolute; top: 640px; left: 0; width: 1200px; text-align: center; font-size: 9.5px; color: var(--text-muted); }
</style>
</head>
<body>
  <div class="city-backdrop" role="img" aria-label="Blurred city shopping street with passers-by at dusk"></div>

  <header class="top-nav">
    <span class="feed-label">Setup your feed</span>
    <div class="feed-select">Active life
      <svg width="11" height="6" viewBox="0 0 11 6"><path d="M1 1l4.5 4L10 1" fill="none" stroke="#b9b8cc" stroke-width="1.3"/></svg>
    </div>
    <nav class="nav-links">
      <a href="#" style="left:943px">How It Works</a>
      <a href="#" style="left:1051px">Login</a>
      <a href="#" style="left:1113px">Sign up</a>
    </nav>
  </header>

  <section class="hero-card">
    <div class="hero-photo" role="img" aria-label="Close-up of chocolate cupcakes in red paper cups"></div>
    <div class="hero-content">
      <div class="brand-name">BrinoKet</div>
      <h1 class="hero-title">Shop directly from your profile</h1>
      <p class="hero-tagline">Save your time. Live better.</p>
      <div class="search-bar">
        <div class="search-input">Search keywords</div>
        <div class="search-button">Search</div>
      </div>
      <div class="social-button"><span class="mark"></span>Sign in with Connectly</div>
      <div class="signup-button">Sign Up</div>
    </div>
  </section>

  <div class="business-button">Go to Business Area
    <svg width="26" height="10" viewBox="0 0 26 10"><path d="M0 5h24M20 1l4 4-4 4" fill="none" stroke="#fff" stroke-width="1.2"/></svg>
  </div>

  <footer>
    <nav class="footer-links">
      <a href="#" class="current" style="left:407px">About Us</a>
      <a href="#" style="left:476px">Blog</a>
      <a href="#" style="left:525px">Business</a>
      <a href="#" style="left:592px">Jobs</a>
      <a href="#" style="left:638px">Privacy</a>
      <a href="#" style="left:700px">FAQ</a>
      <a href="#" style="left:747px">Contacts</a>
    </nav>
    <p class="copyright">© 2015 BrinoKet. All right reserved.</p>
  </footer>
</body>
</html>
```